Branding Pack for new business to business cost saving site

I would like a branding pack for my new project. I would like the following designed;
a4 Presentation folder
Letterhead
Envelope
Business Card
compliment splip

We are a business cost saving site, we have access to 1000s of discount offers for daily business to business offers. I already have the logo therfore please follow th e logo for the coloutr and design.

Target Market(s)

SMEs in United Kingdom

Industry/Entity Type

Business Service

Font styles to use
Serif
Script

Colors
0255a3
fbee3d

Requirements
Must have
• The folder needs to be the same size as attached

```html
<!DOCTYPE html>
<html lang="en">
<head>
<meta charset="utf-8">
<title>tallysave – Stationery</title>
<link rel="stylesheet" href="https://fonts.googleapis.com/css2?family=Quicksand:wght@500&family=Great+Vibes&family=Arimo:wght@400;700&display=swap">
<style>
  :root {
    --navy: #2c3374;
    --yellow: #f9cf45;
    --paper: #ffffff;
    --backdrop: #c9c9c9;
    --wave-light: #e6e6ea;
  }
  * { margin: 0; padding: 0; box-sizing: border-box; }
  html, body { width: 1200px; height: 954px; overflow: hidden; }
  body {
    background: radial-gradient(ellipse at 55% 45%, #f2f2f2 0%, var(--backdrop) 75%);
    position: relative;
    font-family: "Arimo", Arial, sans-serif;
  }
  .brand-name {
    font-family: "Quicksand", sans-serif;
    font-weight: 500;
    letter-spacing: 0.5px;
    line-height: 1;
  }
  .brand-dot {
    display: inline-block;
    border-radius: 50%;
    background: var(--yellow);
    vertical-align: top;
  }
  .tagline {
    font-family: "Arimo", Arial, sans-serif;
    font-size: 6px;
    letter-spacing: 0.6px;
    margin-top: 4px;
    opacity: 0.85;
  }

  /* Folder spread */
  .folder {
    position: absolute;
    left: 70px; top: 32px;
    width: 800px; height: 566px;
    display: flex;
    box-shadow: 0 14px 30px rgba(0,0,0,0.25);
  }
  .folder-back, .folder-front { width: 400px; height: 566px; position: relative; }
  .folder-back { background: var(--paper); }
  .folder-front { background: var(--navy); color: var(--paper); }

  .back-signature {
    position: absolute;
    left: 0; right: 0; bottom: 62px;
    text-align: center;
    color: var(--navy);
  }
  .back-signature .brand-name { font-size: 26px; }
  .back-signature .brand-dot { width: 6px; height: 6px; margin-left: 3px; }
  .back-signature .contact { font-size: 7px; line-height: 1.5; margin-top: 8px; }

  .front-brand {
    position: absolute;
    top: 70px; left: 0; right: 0;
    text-align: center;
  }
  .front-brand .brand-name { font-size: 34px; }
  .front-brand .brand-dot { width: 8px; height: 8px; margin-left: 4px; }
  .front-brand .tagline { font-size: 7px; }
  .front-mark {
    position: absolute;
    left: 180px; top: 330px;
    width: 150px; height: 150px;
    border-radius: 50%;
    background: var(--yellow);
  }

  /* Compliment slip */
  .comp-slip {
    position: absolute;
    left: 590px; top: 658px;
    width: 490px; height: 230px;
    background: var(--paper);
    box-shadow: 0 6px 16px rgba(0,0,0,0.25);
    overflow: hidden;
    color: var(--navy);
  }
  .slip-brand { position: absolute; left: 28px; top: 36px; }
  .slip-brand .brand-name { font-size: 27px; }
  .slip-brand .brand-dot { width: 6px; height: 6px; margin-left: 3px; }
  .slip-contact {
    position: absolute;
    right: 28px; top: 44px;
    text-align: right;
    font-size: 6.5px;
    line-height: 1.4;
  }
  .slip-greeting {
    position: absolute;
    left: 30px; top: 168px;
    font-family: "Great Vibes", cursive;
    font-size: 22px;
  }
  .slip-wave { position: absolute; left: 0; bottom: 0; width: 490px; height: 46px; }
</style>
</head>
<body>
  <section class="folder" aria-label="Presentation folder">
    <div class="folder-back">
      <div class="back-signature">
        <div class="brand-name">tallysave<span class="brand-dot"></span></div>
        <div class="tagline">Smarter spend for firms</div>
        <div class="contact">
          Level 2, 14 Harbour St., Easton QLD 4870 · www.<b>tallysave</b>.com<br>
          <b>T:</b> +61 7 5550 1234 · <b>E:</b> hello@tallysave.com
        </div>
      </div>
    </div>
    <div class="folder-front">
      <div class="front-brand">
        <div class="brand-name">tallysave<span class="brand-dot"></span></div>
        <div class="tagline">Smarter spend for firms</div>
      </div>
      <div class="front-mark"></div>
    </div>
  </section>

  <section class="comp-slip" aria-label="Compliment slip">
    <div class="slip-brand">
      <div class="brand-name">tallysave<span class="brand-dot"></span></div>
      <div class="tagline">Smarter spend for firms</div>
    </div>
    <div class="slip-contact">
      Level 2, 14 Harbour St., Easton QLD 4870<br>
      <b>T:</b> +61 7 5550 1234 · <b>E:</b> hello@tallysave.com<br>
      www.<b>tallysave</b>.com
    </div>
    <div class="slip-greeting">With Compliments</div>
    <svg class="slip-wave" viewBox="0 0 490 46" preserveAspectRatio="none">
      <path d="M0 14 C120 34 260 -6 490 22 L490 46 L0 46 Z" fill="var(--yellow)"/>
      <path d="M0 30 C150 40 300 6 490 28 L490 46 L0 46 Z" fill="var(--wave-light)"/>
      <path d="M150 46 C240 26 360 12 490 34 L490 46 Z" fill="var(--navy)"/>
    </svg>
  </section>
</body>
</html>
```